Enterprise Application UI beautification

We have an enterprise application that is being redesigned. A screenshot from the new UX/UI is provided. The current UI design is OK but we would like it to look better. The key goals of the UI are to look like a premium product (think luxury brand) and for it to be visually very appealing/attractive. When people see the UI we want them to have a significant, positive reaction. They should "ooh" and "ahh". This is a product sold to large enterprises, not consumers. The current UI is a little plain. The colors we want to use are blue, yellow, black, white and gray. We probably don't want different colors but feel free to use any variations within or close to that color scheme that you see fit. Also feel free to modify the spacing, icons, widgets, tables, fonts, etc.

Target Market(s)

Large enterprise customers (Keystone 300).

Number of Pages Required

1 page

Font styles to use
Sans Serif

Colors
3277b5

Requirements
Must have
• A premium feel.

```html
<!DOCTYPE html>
<html lang="en">
<head>
<meta charset="utf-8">
<title>Data Sources – Skyforge Sandbox</title>
<link href="https://fonts.googleapis.com/css2?family=Nunito+Sans:wght@400;600;700&display=swap" rel="stylesheet">
<style>
:root{
  --blue:#3277b5;
  --blue-bright:#3a8fdc;
  --ink:#2a2d34;
  --muted:#5c6270;
  --rail:#17191d;
  --page:#f3f5f8;
  --white:#ffffff;
  --line:#dfe3e9;
  --slate:#474b69;
  --red:#e0353b;
  --green:#37b24d;
  --amber:#e2a316;
  --cyan:#1fb3c9;
  --orange:#f06b1f;
}
*{box-sizing:border-box;margin:0;padding:0}
html,body{width:1200px;height:675px;overflow:hidden}
body{font-family:"Nunito Sans",sans-serif;background:var(--page);color:var(--ink);position:relative}
.abs{position:absolute}
svg{display:block}
.ic{fill:none;stroke:currentColor;stroke-width:1.6;stroke-linecap:round;stroke-linejoin:round}

/* rail */
.rail{left:0;top:0;width:62px;height:675px;background:var(--rail)}
.brand{top:18px;left:0;width:62px;text-align:center;color:#6fb0ea;font-size:11px;font-weight:700;letter-spacing:.5px}
.brand span{display:inline-block;width:6px;height:6px;border-radius:50%;background:#6fb0ea;margin-right:3px;vertical-align:1px}
.rail-item{left:0;width:62px;height:58px;display:flex;align-items:center;justify-content:center;color:#e8ecf2}
.rail-item.active{background:var(--blue-bright)}

/* top bar */
.crumbs{left:77px;top:14px;font-size:12px;color:var(--blue-bright);display:flex;align-items:center;gap:6px}
.user{right:36px;top:14px;font-size:12px;color:var(--ink);display:flex;align-items:center;gap:5px}

/* sources panel */
.sources{left:62px;top:46px;width:250px;height:629px;background:var(--white)}
.panel-title{font-size:16.5px;font-weight:600;color:var(--blue)}
.btn-add{height:21px;border-radius:11px;background:linear-gradient(180deg,#4a9be2,#2f79c2);color:#fff;font-size:10px;display:flex;align-items:center;justify-content:center;gap:4px;box-shadow:0 2px 5px rgba(50,119,181,.35)}
.search{left:81px;top:102px;width:213px;height:25px;border:1px solid #b9bec7;border-radius:13px;font-size:9.5px;color:#8a909b;padding:0 9px;display:flex;align-items:center;justify-content:space-between}
.src{left:62px;width:241px;height:56px;border-bottom:1px solid var(--line);padding:13px 0 0 19px}
.src .name{font-size:12px;color:var(--ink)}
.src .kind{font-size:8.5px;color:var(--blue);margin-top:3px}
.src.active{background:linear-gradient(90deg,#3a8fdc,#2a6fb3);border-bottom:none}
.src.active .name,.src.active .kind{color:#fff}
.scroll{left:306px;top:142px;width:3px;height:125px;background:var(--blue);border-radius:2px}

/* header actions */
.main-title{left:337px;top:62px}
.action{top:64px;font-size:12px;color:var(--blue-bright);display:flex;align-items:center;gap:5px}

/* info card */
.info{left:337px;top:94px;width:838px;height:159px;background:var(--white);box-shadow:0 2px 8px rgba(20,30,50,.05)}
.row{height:32px;display:flex;align-items:center;font-size:11px}
.row .lab{color:var(--muted)}
.row .val{color:var(--blue-bright)}
.col{position:absolute;top:0}
.col .row{border-bottom:1px solid var(--line)}
.col .row:last-child.nob{border-bottom:none}

/* objects */
.obj-title{left:337px;top:281px}
.objects{left:337px;top:314px;width:838px;height:327px;background:var(--white);box-shadow:0 2px 8px rgba(20,30,50,.05)}
.obj{height:32px;border-bottom:1px solid var(--line);display:flex;align-items:center;padding-left:12px;gap:13px;font-size:13px;font-weight:600;color:var(--slate)}
.obj .x{color:var(--red);font-size:13px;margin-left:-6px}
.tog{width:14px;height:14px;border:1px solid var(--blue-bright);color:var(--blue-bright);display:flex;align-items:center;justify-content:center;font-size:12px;line-height:1;font-weight:400}
.obj.open{background:var(--slate);color:#fff;border-bottom:none;position:relative}
.obj.open .tog{border-color:#6fb0ea;color:#6fb0ea}
.fields{position:absolute;right:17px;font-size:12.5px;color:#fff;font-weight:600}
.fields b{color:#5fd36f;font-weight:400}

.tree{left:356px;top:486px;width:1px;height:140px;background:var(--slate)}
.tree-dot{left:353px;top:483px;width:7px;height:7px;border-radius:50%;background:var(--slate)}
.th{top:478px;font-size:11.5px;font-weight:700;color:var(--ink)}
.tline{left:374px;width:788px;height:1px;background:var(--line)}
.cell{font-size:10.5px;color:var(--muted)}
.icons{display:flex;gap:8px;align-items:center;color:#3b4048}
.icons svg{width:14px;height:14px}
.chk{width:14px;height:14px;border:1px solid #8b9bb3;background:#c9d3df;border-radius:1px}
.chk.on{background:var(--blue);border-color:var(--blue);display:flex;align-items:center;justify-content:center}
</style>
</head>
<body>
<svg width="0" height="0" style="position:absolute">
  <defs>
    <symbol id="i-search" viewBox="0 0 16 16"><circle cx="7" cy="7" r="4.6"/><path d="M10.4 10.4 14 14"/></symbol>
    <symbol id="i-copy" viewBox="0 0 16 16"><rect x="5" y="2.5" width="8.5" height="8.5"/><path d="M3 5.5v8h8"/></symbol>
    <symbol id="i-cycle" viewBox="0 0 16 16"><path d="M8 2.5 5.6 6.6M8 2.5l2.4 4.1M3 10.5l-.8 1.6h5M13 10.5l.8 1.6H9M5 12.1 3.6 9.6M12.4 9.6 11 12.1"/></symbol>
    <symbol id="i-target" viewBox="0 0 16 16"><circle cx="8" cy="8" r="4.4"/><path d="M8 1.8v2M8 12.2v2M1.8 8h2M12.2 8h2"/></symbol>
    <symbol id="i-clip" viewBox="0 0 16 16"><rect x="3.5" y="3" width="9" height="11.5" rx="1"/><path d="M6 3V1.8h4V3M8 7v4M6 9h4"/></symbol>
    <symbol id="i-card" viewBox="0 0 16 16"><rect x="1.5" y="4" width="13" height="8.5" rx="1"/><path d="M4 8h4"/></symbol>
    <symbol id="i-user" viewBox="0 0 16 16"><circle cx="8" cy="5.5" r="3"/><path d="M2.8 14.2c.6-3 2.6-4.6 5.2-4.6s4.6 1.6 5.2 4.6z"/></symbol>
    <symbol id="i-pen" viewBox="0 0 16 16"><path d="M11 2.2 13.8 5 5.6 13.2 2.2 13.8l.6-3.4zM9.6 3.6l2.8 2.8"/></symbol>
    <symbol id="i-bin" viewBox="0 0 16 16"><path d="M2.5 4h11M6 4V2.3h4V4M3.8 4l.8 10h6.8l.8-10M6.6 6.5v5M9.4 6.5v5"/></symbol>
  </defs>
</svg>

<!-- navigation rail -->
<nav class="abs rail">
  <div class="abs brand"><span></span>Orin</div>
  <div class="abs rail-item" style="top:99px"><svg class="ic" width="22" height="22" viewBox="0 0 22 22"><circle cx="11" cy="6" r="2.5"/><circle cx="4.5" cy="8" r="2"/><circle cx="17.5" cy="8" r="2"/><path d="M7.5 19v-6a3.5 3.5 0 0 1 7 0v6M2 17v-3.5a2.5 2.5 0 0 1 3.5-2.3M20 17v-3.5a2.5 2.5 0 0 0-3.5-2.3"/></svg></div>
  <div class="abs rail-item" style="top:175px"><svg class="ic" width="22" height="22" viewBox="0 0 22 22"><path d="M6 17h10.5a3.5 3.5 0 0 0 .3-7A5.5 5.5 0 0 0 6.2 9 4 4 0 0 0 6 17z"/></svg></div>
  <div class="abs rail-item active" style="top:253px"><svg class="ic" width="22" height="22" viewBox="0 0 22 22"><rect x="3" y="3" width="14" height="12" rx="1.5"/><path d="M6 18h12V6M3 11h14"/></svg></div>
  <div class="abs rail-item" style="top:330px"><svg class="ic" width="22" height="22" viewBox="0 0 22 22"><rect x="4" y="4" width="14" height="16" rx="1.5"/><path d="M8 4V2.5h6V4M7.5 9h7M7.5 12.5h7M7.5 16l1.5 1.5 3-3"/></svg></div>
  <div class="abs rail-item" style="top:408px"><svg class="ic" width="22" height="22" viewBox="0 0 22 22"><rect x="3" y="4" width="16" height="15" rx="1.5"/><path d="M3 8.5h16M7.5 2v4M14.5 2v4"/><circle cx="15" cy="15" r="3"/><path d="M15 13.8V15h1"/></svg></div>
  <div class="abs rail-item" style="top:486px"><svg class="ic" width="22" height="22" viewBox="0 0 22 22"><circle cx="5" cy="5" r="2.3"/><circle cx="17" cy="17" r="2.3"/><path d="M5 7.3V13a4 4 0 0 0 4 4h5.7M17 14.7V9a4 4 0 0 0-4-4H7.3"/></svg></div>
</nav>

<!-- breadcrumb & user -->
<div class="abs crumbs">
  <svg class="ic" width="15" height="15" viewBox="0 0 16 16"><path d="M2.5 11.5a6 6 0 1 1 11 0M8 10l3-4"/></svg>
  <span>Dashboard</span><span>-</span><span>Menu Name</span>
</div>
<div class="abs user">
  <svg class="ic" width="14" height="14" viewBox="0 0 16 16"><circle cx="8" cy="8" r="2.3"/><path d="M8 1.5v2M8 12.5v2M1.5 8h2M12.5 8h2M3.4 3.4l1.4 1.4M11.2 11.2l1.4 1.4M3.4 12.6l1.4-1.4M11.2 4.8l1.4-1.4"/></svg>
  Dana Wells
  <svg class="ic" width="10" height="10" viewBox="0 0 10 10"><path d="M2 3.5 5 6.5 8 3.5"/></svg>
</div>

<!-- data sources -->
<aside class="abs sources"></aside>
<h2 class="abs panel-title" style="left:81px;top:61px">Data Sources</h2>
<div class="abs btn-add" style="left:237px;top:62px;width:57px">+ ADD</div>
<div class="abs search">Search...<svg class="ic" width="15" height="15" viewBox="0 0 16 16" style="color:var(--blue-bright)"><use href="#i-search"/></svg></div>

<div class="abs src active" style="top:142px"><div class="name">Skyforge - Sandbox</div><div class="kind">Skyforge.io</div></div>
<div class="abs src" style="top:198px"><div class="name">PostBase Test 1 (administration)</div><div class="kind">PostBase SQL</div></div>
<div class="abs src" style="top:254px"><div class="name">PostBase Test 2 (administration)</div><div class="kind">PostBase SQL</div></div>
<div class="abs src" style="top:310px"><div class="name">Sadge</div><div class="kind">Skyforge.io</div></div>
<div class="abs src" style="top:366px"><div class="name">Skyforge Test 1 (masterd ev)</div><div class="kind">PostBase SQL</div></div>
<div class="abs src" style="top:422px"><div class="name">SKF - Field Entry Test</div><div class="kind">Skyforge.io</div></div>
<div class="abs src" style="top:478px"><div class="name">SKF 44</div><div class="kind">Skyforge.io</div></div>
<div class="abs src" style="top:534px"><div class="name">SKF 66</div><div class="kind">Skyforge.io</div></div>
<div class="abs src" style="top:590px"><div class="name">SKF - Field Entry Test</div><div class="kind">Skyforge.io</div></div>
<div class="abs scroll"></div>

<!-- source header -->
<h1 class="abs panel-title main-title">Skyforge - Sandbox</h1>
<div class="abs action" style="left:763px"><svg class="ic" width="15" height="15"><use href="#i-pen"/></svg>Edit</div>
<div class="abs action" style="left:856px"><svg class="ic" width="15" height="15" viewBox="0 0 16 16"><path d="M13 9a5 5 0 1 1-2-5.5"/><circle cx="11.5" cy="4.5" r="1.8"/></svg>Clone</div>
<div class="abs action" style="left:959px"><svg class="ic" width="15" height="15"><use href="#i-bin"/></svg>Delete</div>
<div class="abs action" style="left:1065px"><svg class="ic" width="14" height="15" viewBox="0 0 16 16"><path d="M9.5 1.5 3.5 9h4l-1 5.5 6-7.5h-4z"/></svg>Test Connection</div>

<section class="abs info">
  <div class="col" style="left:13px;width:394px">
    <div class="row"><span class="lab" style="width:251px;padding-left:10px">Date Source Name :</span><span class="val">Skyforge - Sandbox</span></div>
    <div class="row"><span class="lab" style="width:251px;padding-left:10px">Date Source Type :</span><span class="val">Application</span></div>
    <div class="row"><span class="lab" style="width:251px;padding-left:10px">Status :</span><span class="val">Active</span></div>
    <div class="row"><span class="lab" style="width:251px;padding-left:10px">Created By :</span><span class="val">harlow.test</span></div>
    <div class="row nob"><span class="lab" style="width:251px;padding-left:10px">Last Updated By :</span><span class="val">harlow.test</span></div>
  </div>
  <div class="col" style="left:425px;width:394px">
    <div class="row"><span class="lab" style="width:219px;padding-left:10px">User Name :</span><span class="val">opsdev@dev.brightlane.net</span></div>
    <div class="row"><span class="lab" style="width:219px;padding-left:10px">Security Token :</span><span class="val">tadkaji4234ifndkn3</span></div>
    <div class="row"><span class="lab" style="width:219px;padding-left:10px">Environment Type :</span><span class="val">Production</span></div>
    <div class="row"><span class="lab" style="width:219px;padding-left:10px">Connected App :</span><span class="val">No</span></div>
  </div>
</section>

<!-- data objects -->
<h2 class="abs panel-title obj-title">Data Objects</h2>
<div class="abs btn-add" style="left:480px;top:281px;width:56px">+ ADD</div>

<section class="abs objects">
  <div class="obj"><span class="tog">+</span>Account<span class="x">✕</span></div>
  <div class="obj"><span class="tog">+</span>Asset<span class="x">✕</span></div>
  <div class="obj"><span class="tog">+</span>Asset Relationship<span class="x">✕</span></div>
  <div class="obj"><span class="tog">+</span>Asset Token Event<span class="x">✕</span></div>
  <div class="obj open"><span class="tog">−</span>Case<span class="x">✕</span><span class="fields">Fields <b>+</b>Add</span></div>
</section>

<div class="abs tree-dot"></div>
<div class="abs tree"></div>
<div class="abs th" style="left:374px">Field Name</div>
<div class="abs th" style="left:537px">Data Type</div>
<div class="abs th" style="left:721px">Rule Types</div>
<div class="abs th" style="left:876px">Primary Key</div>
<div class="abs th" style="left:989px">Sensitive Data</div>
<div class="abs th" style="left:1114px">Actions</div>
<div class="abs tline" style="top:502px"></div>
<div class="abs tline" style="top:536px"></div>
<div class="abs tline" style="top:569px"></div>
<div class="abs tline" style="top:603px"></div>

<!-- row 1 -->
<div class="abs cell" style="left:374px;top:512px">Account Description</div>
<div class="abs cell" style="left:537px;top:512px">Common Text</div>
<div class="abs icons ic" style="left:719px;top:512px"><b style="font:700 15px 'Nunito Sans',sans-serif;color:var(--blue);stroke:none;width:14px">a</b><svg><use href="#i-search"/></svg><svg><use href="#i-copy"/></svg><svg><use href="#i-cycle"/></svg><svg><use href="#i-target"/></svg><svg viewBox="0 0 16 16" style="fill:currentColor;stroke:none"><path d="M6 4.5 10.5 8 6 11.5z"/></svg></div>
<div class="abs chk on" style="left:904px;top:512px"><svg width="10" height="10" viewBox="0 0 10 10" class="ic" style="color:#fff"><path d="M2 5.2 4.2 7.4 8 2.8"/></svg></div>
<div class="abs icons ic" style="left:992px;top:512px;gap:17px"><svg><use href="#i-clip"/></svg><svg><use href="#i-card"/></svg><svg><use href="#i-user"/></svg></div>
<div class="abs icons ic" style="left:1114px;top:511px;gap:16px"><svg style="width:15px;height:15px;color:var(--blue-bright)"><use href="#i-pen"/></svg><svg style="width:15px;height:15px;color:var(--red)"><use href="#i-bin"/></svg></div>

<!-- row 2 -->
<div class="abs cell" style="left:374px;top:546px">Account Fax</div>
<div class="abs cell" style="left:537px;top:546px">Address. Address Line 3</div>
<div class="abs icons ic" style="left:719px;top:546px"><b style="font:700 15px 'Nunito Sans',sans-serif;color:#3b4048;stroke:none;width:14px">a</b><svg style="color:var(--amber)"><use href="#i-search"/></svg><svg><use href="#i-copy"/></svg><svg><use href="#i-cycle"/></svg><svg style="color:var(--cyan)"><use href="#i-target"/></svg><svg viewBox="0 0 16 16" style="fill:currentColor;stroke:none"><path d="M6 4.5 10.5 8 6 11.5z"/></svg></div>
<div class="abs chk" style="left:904px;top:546px"></div>
<div class="abs icons ic" style="left:1114px;top:545px;gap:16px"><svg style="width:15px;height:15px;color:var(--blue-bright)"><use href="#i-pen"/></svg><svg style="width:15px;height:15px;color:var(--red)"><use href="#i-bin"/></svg></div>

<!-- row 3 -->
<div class="abs cell" style="left:374px;top:580px">Account ID</div>
<div class="abs cell" style="left:537px;top:580px">Common ID</div>
<div class="abs icons ic" style="left:719px;top:580px"><b style="font:700 15px 'Nunito Sans',sans-serif;color:#3b4048;stroke:none;width:14px">a</b><svg><use href="#i-search"/></svg><svg style="color:var(--green)"><use href="#i-copy"/></svg><svg><use href="#i-cycle"/></svg><svg><use href="#i-target"/></svg><svg viewBox="0 0 16 16" style="fill:var(--orange);stroke:none"><path d="M6 4.5 10.5 8 6 11.5z"/></svg></div>
<div class="abs chk" style="left:904px;top:580px"></div>
<div class="abs icons ic" style="left:992px;top:580px;gap:17px"><svg><use href="#i-clip"/></svg><svg><use href="#i-card"/></svg><svg><use href="#i-user"/></svg></div>
<div class="abs icons ic" style="left:1114px;top:579px;gap:16px"><svg style="width:15px;height:15px;color:var(--blue-bright)"><use href="#i-pen"/></svg><svg style="width:15px;height:15px;color:var(--red)"><use href="#i-bin"/></svg></div>

<!-- row 4 -->
<div class="abs cell" style="left:374px;top:614px">Account Name</div>
<div class="abs cell" style="left:537px;top:614px">Address. Address Line 2</div>
<div class="abs icons ic" style="left:719px;top:614px"><b style="font:700 15px 'Nunito Sans',sans-serif;color:#3b4048;stroke:none;width:14px">a</b><svg><use href="#i-search"/></svg><svg><use href="#i-copy"/></svg><svg style="color:var(--red)"><use href="#i-cycle"/></svg><svg><use href="#i-target"/></svg><svg viewBox="0 0 16 16" style="fill:currentColor;stroke:none"><path d="M6 4.5 10.5 8 6 11.5z"/></svg></div>
<div class="abs chk" style="left:904px;top:614px"></div>
<div class="abs icons ic" style="left:1114px;top:613px;gap:16px"><svg style="width:15px;height:15px;color:var(--blue-bright)"><use href="#i-pen"/></svg><svg style="width:15px;height:15px;color:var(--red)"><use href="#i-bin"/></svg></div>
</body>
</html>
```